The Polish & Glow Studio Website Update

Hello. I am seeking to freshen up my website with a clean and easy feel that incorporates our modern chic style. Our services cater to mostly young professionals and modern moms.

We focus on natural nail care and gentle professional waxing. We are known for our cleanliness. Our clients like our current website, however I'm hoping to make it look even more professional and user friendly. Some clients have even said our current website feels welcoming, unlike other websites that in they feel give a snobbish vibe. I like clean lines, simple, fresh, and sometimes bold. Totally NOT a fan of whimsical.

I threw added an accent color to the color pallet...however it should be used in moderation. I am also open to other accent colors. I'd like the site to emphasize the Brazilian wax as much as nails, if not more than nail. The photos downloaded are just to give you a few images of who we are, however are not necessary. Current website www.thepolishandglowstudio.example

Target Market(s)

Females 30-55

Industry/Entity Type

Beauty Salon

Coding

Coded - Design and coding required

Number of Pages Required

5+ page

Font styles to use
Sans Serif

Colors
ffffff
1b1b1b
acd136
eeeeee
878787
c4c4c4
efefef
7f7f7f

Requirements
Must have
• Clean look
Nice to have
• Our logo
Should not have
• Whimsical

```html
<!DOCTYPE html>
<html lang="en">
<head>
<meta charset="utf-8">
<title>The Polish &amp; Glow Studio</title>
<link href="https://fonts.googleapis.com/css2?family=Oswald:wght@300;400&family=Open+Sans:wght@400;600;700&display=swap" rel="stylesheet">
<style>
:root{
  --white:#ffffff;
  --ink:#1b1b1b;
  --lime:#acd136;
  --mist:#eeeeee;
  --grey:#878787;
  --silver:#c4c4c4;
  --paper:#f3f5f7;
  --stone:#7f7f7f;
  --charcoal:#2b2b2b;
}
*{box-sizing:border-box;margin:0;padding:0}
html,body{width:1200px;height:2691px;overflow:hidden}
body{position:relative;background:var(--white);font-family:"Open Sans",Arial,sans-serif;color:var(--grey)}
.display{font-family:"Oswald",Arial,sans-serif;font-weight:300;text-transform:uppercase}

/* header */
.header{position:absolute;top:0;left:0;width:1200px;height:102px;border-top:4px solid var(--lime);background:var(--white)}
.social-top{position:absolute;left:86px;top:30px;display:flex;gap:9px}
.social-top span,.follow span{border-radius:50%;display:flex;align-items:center;justify-content:center}
.social-top span{width:36px;height:36px;border:1px solid var(--silver)}
.social-top span::after{content:"";width:9px;height:9px;border-radius:50%;background:var(--silver)}
.brand{position:absolute;left:0;width:1200px;top:28px;text-align:center;font-weight:600;font-size:30px;color:#555;letter-spacing:-.5px}
.tools{position:absolute;right:86px;top:30px;display:flex;gap:12px}
.tools span{width:40px;height:40px;border:1px solid var(--silver);border-radius:50%;display:flex;align-items:center;justify-content:center}
.tools span.search{border-color:var(--lime)}

/* hero */
.hero{position:absolute;top:102px;left:0;width:1200px;height:485px;
  background:
    linear-gradient(90deg,rgba(70,55,40,.35) 0%,rgba(0,0,0,0) 22%,rgba(0,0,0,0) 62%,rgba(25,25,25,.55) 78%,rgba(20,20,20,.7) 100%),
    linear-gradient(180deg,#d9d6d0 0%,#c5c1ba 30%,#8d9466 52%,#6f7d45 66%,#4a4a40 82%,#2e2b28 100%)}
.hero h1{position:absolute;top:180px;width:100%;text-align:center;font-size:56px;color:var(--white);letter-spacing:1px;text-shadow:0 1px 3px rgba(0,0,0,.3)}
.hero h1 b{font-weight:300;color:var(--lime)}
.hero p{position:absolute;top:262px;left:250px;width:700px;text-align:center;color:var(--white);font-size:12.5px;line-height:27px;text-shadow:0 1px 2px rgba(0,0,0,.4)}
.dots{position:absolute;top:447px;width:100%;display:flex;justify-content:center;gap:6px}
.dots i{width:9px;height:9px;border-radius:50%;background:var(--lime)}
.dots i.on{background:var(--white)}

/* nav */
.nav{position:absolute;top:587px;left:0;width:1200px;height:59px;background:var(--lime);border-bottom:4px solid var(--ink)}
.nav a{position:absolute;top:0;height:55px;line-height:55px;color:var(--white);font-size:12px;text-decoration:none;text-transform:uppercase}
.nav a.current{left:86px;width:101px;text-align:center;background:var(--ink)}

/* intro */
.intro-brand{position:absolute;top:718px;left:111px;width:262px;text-align:center;font-weight:600;font-size:30px;color:#555;line-height:38px}
.intro-text{position:absolute;top:699px;left:443px;width:660px;font-size:12px;line-height:26px;color:var(--stone)}

/* appointment */
.appt-photo{position:absolute;top:852px;left:0;width:601px;height:504px;
  background:
    linear-gradient(90deg,rgba(40,40,40,.35) 0%,rgba(0,0,0,0) 25%,rgba(0,0,0,0) 80%,rgba(30,30,30,.25) 100%),
    linear-gradient(180deg,#e9e6e0 0%,#d9d4cc 35%,#c9c2b6 55%,#6d6a66 75%,#3f3d3b 100%)}
.appt{position:absolute;top:852px;left:601px;width:599px;height:504px;background:var(--ink);color:var(--white)}
.appt h2{position:absolute;left:66px;top:28px;font-size:26px}
.divider{position:absolute;width:76px;height:12px}
.appt h3{position:absolute;left:66px;top:108px;font-family:"Oswald",Arial,sans-serif;font-weight:400;font-size:17px}
.appt p{position:absolute;left:66px;top:146px;width:350px;font-size:11.5px;line-height:22px;color:#cfcfcf}
.field{position:absolute;left:66px;width:343px;height:41px;background:var(--white);color:var(--ink);font-size:11px;line-height:41px;padding-left:12px;text-transform:uppercase}
.field svg{position:absolute;right:12px;top:14px}
.btn{position:absolute;background:var(--lime);color:var(--white);font-size:11.5px;text-transform:uppercase;display:flex;align-items:center;justify-content:center;gap:6px}
.vertical{position:absolute;left:430px;top:422px;width:200px;transform:rotate(-90deg);transform-origin:0 0;font-size:19px;font-family:"Oswald",Arial,sans-serif;font-weight:400;letter-spacing:1.5px;color:var(--white)}

/* services */
.section-title{position:absolute;width:1200px;text-align:center;font-size:27px;color:var(--ink)}
.svc-lead{position:absolute;top:1464px;width:1200px;text-align:center;font-size:16px;line-height:34px;color:#444}
.svc-lead em{font-style:normal;color:var(--lime)}
.cards{position:absolute;top:1555px;left:0;width:1200px;display:flex;gap:2px}
.card{width:299px}
.card .photo{height:347px}
.card .label{height:68px;background:var(--lime);color:var(--white);text-align:center;padding-top:10px;font-size:17px;line-height:24px}
.arrows{position:absolute;top:2006px;left:560px;display:flex;gap:10px}
.arrows span{width:34px;height:34px;border:1px solid var(--silver);display:flex;align-items:center;justify-content:center}

/* promo */
.promo{position:absolute;top:2067px;left:0;width:1200px;height:412px;background:var(--paper)}
.promo-box{position:absolute;top:50px;left:86px;width:574px;height:290px;background:var(--white);border:1px solid var(--silver);box-shadow:0 0 6px rgba(0,0,0,.08);padding:6px}
.strip{display:flex;gap:3px;height:198px}
.strip div{flex:1}
.promo-box h4{text-align:center;font-weight:600;font-size:29px;color:var(--ink);margin-top:6px}
.promo-box small{display:block;text-align:center;font-size:18px;color:var(--ink)}
.promo h2{position:absolute;left:698px;top:52px;font-size:27px;color:var(--ink)}
.promo h3{position:absolute;left:698px;top:120px;font-size:25px;color:var(--lime)}
.promo h3 b{font-weight:400;color:var(--ink)}
.promo p{position:absolute;left:698px;top:174px;width:430px;font-size:11.5px;line-height:27px;color:var(--stone)}

/* footer */
.footer{position:absolute;top:2479px;left:0;width:1200px;height:158px;background:var(--charcoal);color:var(--white)}
.footer h5{position:absolute;top:34px;font-weight:400;font-size:16px;text-transform:uppercase}
.footer .line{position:absolute;font-size:12px;line-height:20px;color:#e6e6e6}
.footer .email{position:absolute;left:569px;top:65px;width:211px;height:39px;background:var(--white);color:var(--grey);font-size:11px;line-height:39px;padding-left:12px}
.follow{position:absolute;left:938px;top:64px;display:flex;gap:7px}
.follow span{width:40px;height:40px;border:2px solid var(--white)}
.follow span::after{content:"";width:9px;height:9px;border-radius:50%;background:var(--white)}
.copyright{position:absolute;top:2637px;left:0;width:1200px;height:54px;background:linear-gradient(180deg,#bde04a,var(--lime));color:var(--white);text-align:center;font-size:11.5px;line-height:54px}
</style>
</head>
<body>

<header class="header">
  <div class="social-top"><span></span><span></span><span></span><span></span></div>
  <div class="brand">The Polish &amp; Glow Studio</div>
  <div class="tools">
    <span class="search"><svg width="14" height="14" viewBox="0 0 14 14"><circle cx="6" cy="6" r="4.2" fill="none" stroke="#acd136" stroke-width="2"/><line x1="9" y1="9" x2="13" y2="13" stroke="#acd136" stroke-width="2"/></svg></span>
    <span><svg width="16" height="14" viewBox="0 0 16 14"><path d="M1 1h3l2 8h8l1.5-6H5" fill="none" stroke="#878787" stroke-width="1.6"/><circle cx="7" cy="12" r="1.3" fill="#878787"/><circle cx="13" cy="12" r="1.3" fill="#878787"/></svg></span>
  </div>
</header>

<section class="hero" role="img" aria-label="Treatment room with a waxing bed covered in a green towel">
  <h1 class="display">The Polish <b>&amp;</b> Glow Studio</h1>
  <p>To be the #1 nail and wax salon in the Maplebrook, CT area, offering the most meticulous manicures, pedicures, and waxing service. We use superior products, advanced techniques, and exceptional sanitation procedures to provide and friendly staff is always happy to assist with any of your Polish &amp; Glow concerns.</p>
  <div class="dots"><i></i><i></i><i class="on"></i><i></i><i></i></div>
</section>

<nav class="nav">
  <a class="current" href="#">Home</a>
  <a href="#" style="left:208px">Schedule an appointment</a>
  <a href="#" style="left:432px">Products &amp; Services</a>
  <a href="#" style="left:617px">Careers</a>
  <a href="#" style="left:718px">Specials</a>
  <a href="#" style="left:820px">About us</a>
  <a href="#" style="left:929px">FAQ</a>
  <a href="#" style="left:999px">Contact us</a>
</nav>

<div class="intro-brand">The Polish &amp;<br>Glow Studio</div>
<p class="intro-text">To be the #1 nail and wax salon in the Maplebrook, CT area, offering the most meticulous manicures, pedicures, and waxing service. We use superior products, advanced techniques, and exceptional sanitation procedures to provide our clients with safe, quality services. Our knowledgeable and friendly staff is always happy to assist with any of your another Licensed Nail Technician to our team Polish &amp; Glow concerns.</p>

<div class="appt-photo" role="img" aria-label="Bright salon interior with pedicure chairs and a wall of nail polish"></div>
<section class="appt">
  <h2 class="display">Make an appointment</h2>
  <svg class="divider" style="left:66px;top:74px" viewBox="0 0 76 12"><line x1="0" y1="6" x2="76" y2="6" stroke="#acd136" stroke-width="1.5"/><circle cx="6" cy="6" r="4" fill="#1b1b1b" stroke="#acd136" stroke-width="1.5"/><circle cx="38" cy="6" r="4" fill="#1b1b1b" stroke="#acd136" stroke-width="1.5"/><circle cx="70" cy="6" r="4" fill="#1b1b1b" stroke="#acd136" stroke-width="1.5"/></svg>
  <h3>INTRODUCTIONS</h3>
  <p>We are excited to welcome another Licensed Nail Technician to our team, Dana Whitfield. Dana has over 25 years experience and is also a ness. If you're seeking a perfect mani, Dana is your girl.</p>
  <div class="field" style="top:244px">Name:</div>
  <div class="field" style="top:292px">Email:</div>
  <div class="field" style="top:339px">Select date:<svg width="12" height="12" viewBox="0 0 12 12"><rect x="1" y="2" width="10" height="9" fill="none" stroke="#1b1b1b"/><line x1="1" y1="5" x2="11" y2="5" stroke="#1b1b1b"/></svg></div>
  <div class="field" style="top:387px">Select time:<svg width="12" height="12" viewBox="0 0 12 12"><circle cx="6" cy="6" r="5" fill="none" stroke="#1b1b1b"/><path d="M6 3v3h2" fill="none" stroke="#1b1b1b"/></svg></div>
  <div class="btn" style="left:70px;top:434px;width:113px;height:40px">Book now</div>
  <div class="vertical">ONLINE BOOKING &#8249;</div>
</section>

<h2 class="section-title display" style="top:1386px">Service menu</h2>
<svg class="divider" style="left:562px;top:1434px" viewBox="0 0 76 12"><line x1="0" y1="6" x2="76" y2="6" stroke="#acd136" stroke-width="1.5"/><circle cx="6" cy="6" r="4" fill="#fff" stroke="#acd136" stroke-width="1.5"/><circle cx="38" cy="6" r="4" fill="#fff" stroke="#acd136" stroke-width="1.5"/><circle cx="70" cy="6" r="4" fill="#fff" stroke="#acd136" stroke-width="1.5"/></svg>
<p class="svc-lead display"><em>Facials are now available at the Polish &amp; Glow Studio</em>. Our signature facial is<br>meticulously to your skin's needs be it quenching your <em>skin's thirst</em>, clearing</p>

<div class="cards">
  <div class="card"><div class="photo" role="img" aria-label="Hands with a fresh French manicure" style="background:linear-gradient(170deg,#f4f1ee 0%,#e9d3c6 40%,#d9ad98 70%,#f0ebe7 100%)"></div><div class="label display">Signature manicure<br>$24.00</div></div>
  <div class="card"><div class="photo" role="img" aria-label="Client receiving a signature facial" style="background:linear-gradient(90deg,#6b4a3a 0%,#c99c84 35%,#eadfd7 60%,#f3eee9 100%)"></div><div class="label display">Signature facial<br>$34.00</div></div>
  <div class="card"><div class="photo" role="img" aria-label="Close-up of defined brows and eye makeup" style="background:linear-gradient(160deg,#2f2622 0%,#c9a28c 30%,#ead6c8 65%,#d9b4a0 100%)"></div><div class="label display">Brow design<br>$13.00</div></div>
  <div class="card"><div class="photo" role="img" aria-label="Model with red lips and red nails" style="background:linear-gradient(100deg,#2e2624 0%,#5a4038 30%,#c99a86 55%,#8a5a4c 80%,#2b2422 100%)"></div><div class="label display">Lip<br>$55.00</div></div>
</div>
<div class="arrows">
  <span><svg width="8" height="10" viewBox="0 0 8 10"><path d="M6 1L2 5l4 4" fill="none" stroke="#878787" stroke-width="1.5"/></svg></span>
  <span><svg width="8" height="10" viewBox="0 0 8 10"><path d="M2 1l4 4-4 4" fill="none" stroke="#878787" stroke-width="1.5"/></svg></span>
</div>

<section class="promo">
  <div class="promo-box">
    <div class="strip">
      <div role="img" aria-label="Smooth legs after waxing" style="background:linear-gradient(160deg,#fbf9f7 0%,#ecdcd0 55%,#d7b9a6 100%)"></div>
      <div role="img" aria-label="Close-up of a groomed brow and eye" style="background:linear-gradient(180deg,#d9b9a5 0%,#b58f79 50%,#e3cbbb 100%)"></div>
      <div role="img" aria-label="Wax strip being applied" style="background:linear-gradient(180deg,#e6d0c2 0%,#f4ede6 50%,#c9a893 100%)"></div>
      <div role="img" aria-label="Smooth skin after treatment" style="background:linear-gradient(160deg,#f7f2ee 0%,#e6cfbf 60%,#dcc1b0 100%)"></div>
    </div>
    <h4>The Polish &amp; Glow Studio</h4>
    <small>Limited time offer!</small>
  </div>
  <h2 class="display">Schedule now online</h2>
  <svg class="divider" style="left:698px;top:102px" viewBox="0 0 76 12"><line x1="0" y1="6" x2="76" y2="6" stroke="#acd136" stroke-width="1.5"/><circle cx="6" cy="6" r="4" fill="#f3f5f7" stroke="#acd136" stroke-width="1.5"/><circle cx="38" cy="6" r="4" fill="#f3f5f7" stroke="#acd136" stroke-width="1.5"/><circle cx="70" cy="6" r="4" fill="#f3f5f7" stroke="#acd136" stroke-width="1.5"/></svg>
  <h3 class="display">Up to <b>25%</b> off select services</h3>
  <p>As a coach and consultant my philosophy to success is practical, strategic and spiritual. I studied Life and Business Management at Harborview College, where my self-designed degree allowed me to focus on my life coach the chances of entrepreneurial success.......</p>
  <div class="btn" style="left:698px;top:303px;width:129px;height:40px">Click here <svg width="12" height="12" viewBox="0 0 12 12"><circle cx="6" cy="6" r="5" fill="none" stroke="#fff" stroke-width="1.4"/><path d="M5 3.5L7.5 6 5 8.5" fill="none" stroke="#fff" stroke-width="1.4"/></svg></div>
</section>

<footer class="footer">
  <h5 style="left:99px">Contact us</h5>
  <div class="line" style="left:99px;top:68px">42 Linden Lane<br>Maplebrook, CT 06400</div>
  <div class="line" style="left:328px;top:68px">(555) 014-2038<br>info@thepolishandglowstudio.example</div>
  <h5 style="left:569px">Newsletter</h5>
  <div class="email">Email:</div>
  <div class="btn" style="left:789px;top:65px;width:92px;height:39px;font-size:10.5px;font-weight:700">Subscribe</div>
  <h5 style="left:944px">Follow us</h5>
  <div class="follow"><span></span><span></span><span></span><span></span></div>
</footer>
<div class="copyright">Copyright © 2016 The Polish &amp; Glow Studio all rights are reserved</div>

</body>
</html>
```